I want a website to be designed for our new company, it's an import and export company for variety of things.

please see the attached Logo for our company and the Images for our different sections for our busienss

Target Market(s)

multiple

Coding

Coded - Design and coding required

Number of Pages Required

5+ page

Font styles to use
Sans Serif

Colors

Designer to choose colors to be used in the design.

Requirements
Must have
• KVR GLOBALINKS
• KVR globalinks Trading & Contracting provides various services. The Company offers infrastructure construction, oil, enegy and gas services, agricultural projects, real estate development, travel and tourism, and food processing and trading.
• Civil contracting for infrastructure, residential and heavy projects. Through its main subsidiaries; distribution of general food products, construction chemicals including corrosion inhibitors and electrical machinery; provides catering and travel agency services; ownership and operation of a school; offers human sources services including manpower supply.
• Drilling and Gold Mines Used Machinery, All Kinds of Construction Machinery, Drilling Machines are manufactured and sold.
Nice to have
• good designa and beautiful colours, it has too look professional

```html
<!DOCTYPE html>
<html lang="en">
<head>
<meta charset="utf-8">
<title>KVR Globalinks – Home Page Themes</title>
<link rel="stylesheet" href="https://fonts.googleapis.com/css2?family=Roboto+Slab:wght@500;700&family=Roboto:wght@400;500;700&display=swap">
<style>
:root{
  --stage:#c6c6c6;
  --gold:#c8922a;
  --gold-deep:#b47e1e;
  --red:#c8102e;
  --black:#0d0d0d;
  --white:#ffffff;
  --slab:"Roboto Slab", Georgia, serif;
  --sans:"Roboto", Arial, sans-serif;
}
*{margin:0;padding:0;box-sizing:border-box}
html,body{width:734px;height:1200px;overflow:hidden;background:var(--stage)}
.stage{position:absolute;left:0;top:0;width:1507px;height:2464px;transform:scale(.48706);transform-origin:0 0;background:var(--stage);font-family:var(--sans)}
.page{
  position:absolute;top:84px;width:639px;height:2296px;overflow:hidden;
  --services-bg:#1b1b1b;--about-bg:#0e0e0e;--feature-bg:#c9962b;--news-bg:#0f0f0f;
  --title:#ffffff;--body:#d6d6d6;--muted:#bdbdbd;--ring:#e8e8e8;
  box-shadow:0 4px 18px rgba(0,0,0,.25)
}
.page.dark{left:76px}
.page.light{
  left:792px;
  --services-bg:#e7e7e7;--about-bg:#ffffff;--feature-bg:#c91a2d;--news-bg:#ffffff;
  --title:#151515;--body:#555555;--muted:#777777;--ring:var(--gold)
}
.abs{position:absolute}
.center{text-align:center}

/* header */
.site-header{left:0;top:0;width:639px;height:68px;background:var(--black);border-top:2px solid var(--gold-deep)}
.brand{left:52px;top:20px;display:flex;align-items:center;gap:6px;color:#f2f2f2;font:700 13px/1 var(--sans);letter-spacing:.5px}
.brand i{width:12px;height:12px;border-radius:50%;border:1.5px solid var(--gold)}
.login{left:455px;top:10px;width:52px;height:20px;border:1px solid var(--gold);border-radius:10px;color:var(--gold);font:400 8px/18px var(--sans);text-align:center}
.lang{left:528px;top:14px;color:#ddd;font:400 8px/1 var(--sans)}
.lang b{display:inline-block;width:5px;height:5px;border-radius:50%;background:var(--red);margin-right:4px}
.nav{left:230px;top:47px;display:flex;gap:17px;font:500 8px/1 var(--sans);color:#fff}
.nav .active{color:var(--gold)}

/* hero */
.hero{left:0;top:68px;width:639px;height:295px;background:linear-gradient(180deg,#2d4f9c 0%,#5f86c8 30%,#c9a9a0 55%,#7a4a3c 68%,#25303f 82%,#1b2433 100%)}
.hero-title{left:0;top:148px;width:639px;color:#fff;font:700 27px/1 var(--slab);text-align:center;letter-spacing:.5px}
.hero-text{left:130px;top:194px;width:380px;color:#fff;font:400 9.5px/15px var(--sans);text-align:center}
.btn-solid{background:var(--gold);color:#fff;border-radius:16px;font:700 9px/1 var(--sans);display:flex;align-items:center;justify-content:center;gap:5px}
.hero-btn{left:266px;top:244px;width:108px;height:32px}
.arrow-ring{width:22px;height:22px;border:1px solid #fff;border-radius:50%}

/* services */
.services{left:0;top:363px;width:639px;height:490px;background:var(--services-bg)}
.sec-title{color:var(--title);font:700 20px/1 var(--slab);text-align:center;width:639px;left:0}
.sec-text{color:var(--body);font:400 7.5px/14px var(--sans);text-align:center}
.tabs{left:164px;top:517px;width:311px;height:37px;border:1px solid var(--gold);border-radius:19px;display:flex;overflow:visible}
.tab{flex:1;display:flex;align-items:center;gap:8px;padding-left:20px;font:500 7.5px/12px var(--sans);color:var(--title)}
.tab.on{background:var(--gold);color:#fff;border-radius:18px 0 0 18px;position:relative}
.tab.on:after{content:"";position:absolute;left:72px;bottom:-6px;border:6px solid transparent;border-bottom:0;border-top-color:var(--gold)}
.svc-card{top:620px;width:121px;height:104px;background:#fff;text-align:center;box-shadow:0 2px 6px rgba(0,0,0,.12)}
.svc-icon{position:absolute;left:34px;top:-27px;width:53px;height:53px;border-radius:50%;background:var(--red);border:2px solid #fff}
.svc-card h3{margin-top:37px;font:500 9.5px/1 var(--sans);color:#222}
.svc-card p{margin:8px 6px 0;font:400 7px/12px var(--sans);color:#777}
.btn-line{border:1.5px solid var(--gold);color:var(--gold);border-radius:15px;font:500 7.5px/1 var(--sans);display:flex;align-items:center;justify-content:center;gap:4px}

/* video band */
.band{left:0;top:853px;width:639px;height:253px;background:linear-gradient(120deg,#b7652c 0%,#8b5a3a 35%,#6c5a4a 55%,#c99b2c 75%,#5d4a3a 100%)}
.play{left:59px;top:923px;width:46px;height:46px;border:1.5px solid #fff;border-radius:50%}
.band-text{left:59px;top:997px;color:#fff;font:700 14.5px/21px var(--slab)}

/* about */
.about{left:0;top:1106px;width:639px;height:351px;background:var(--about-bg)}
.about-photo{left:62px;top:1190px;width:196px;height:196px;border-radius:50%;border:2px solid var(--ring);padding:8px}
.about-photo div{width:100%;height:100%;border-radius:50%;background:radial-gradient(circle at 45% 50%,#d07a3a 0%,#2f5a68 35%,#1f3b40 70%)}
.about-title{left:320px;top:1186px;color:var(--title);font:700 19px/1 var(--slab)}
.about-text{left:320px;top:1222px;width:260px;color:var(--body);font:400 7.5px/15px var(--sans);text-align:justify}
.about-btn{left:320px;top:1346px;width:89px;height:26px;font-size:7.5px}

/* featured */
.feature-band{left:0;top:1457px;width:639px;height:249px;background:var(--feature-bg)}
.feature-base{left:0;top:1706px;width:639px;height:392px;background:var(--news-bg)}
.feature-title{color:#fff}
.proj{top:1568px;width:160px;height:166px;overflow:hidden;box-shadow:0 3px 8px rgba(0,0,0,.25)}
.proj .cap{position:absolute;left:0;bottom:0;width:100%;height:64px;background:linear-gradient(180deg,rgba(0,0,0,0),rgba(0,0,0,.85) 40%);text-align:center;color:#fff}
.proj h4{margin-top:14px;font:500 9px/1 var(--sans)}
.proj p{margin-top:6px;font:400 6.5px/11px var(--sans);color:#ddd}
.chev{color:#fff;font:400 16px/1 var(--sans)}

/* news */
.news{top:1838px;width:165px}
.news .img{height:104px;position:relative}
.news .date{position:absolute;left:0;bottom:0;width:100%;height:14px;background:rgba(200,146,42,.9);color:#fff;font:500 6.5px/14px var(--sans);padding-left:10px}
.news h4{margin:13px 9px 0;color:var(--title);font:500 8px/13px var(--sans)}
.news p{margin:6px 9px 0;color:var(--muted);font:400 6.5px/12px var(--sans);text-align:justify}
.news .more{display:block;margin:9px 9px 0;color:var(--gold);font:700 6.5px/1 var(--sans)}

/* footer */
.footer{left:0;top:2098px;width:639px;height:198px;background:linear-gradient(180deg,#151515,#0b0b0b)}
.foot-brand{left:0;top:2150px;width:639px;display:flex;justify-content:center;align-items:center;gap:6px;color:#eee;font:700 12px/1 var(--sans);letter-spacing:.5px}
.foot-brand i{width:11px;height:11px;border-radius:50%;border:1.5px solid var(--gold)}
.foot-contact{left:0;top:2195px;width:639px;display:flex;justify-content:center;gap:24px;color:#fff;font:400 7px/1 var(--sans)}
.foot-contact span{display:flex;align-items:center;gap:4px}
.foot-links{left:0;top:2216px;width:639px;color:#ddd;font:400 6.5px/1 var(--sans);text-align:center;word-spacing:2px}
.foot-copy{left:0;top:2235px;width:639px;color:#ccc;font:400 6.5px/1 var(--sans);text-align:center}
.socials{left:272px;top:2257px;display:flex;gap:6px}
.socials i{width:19px;height:19px;border:1px solid #ddd;border-radius:50%}
</style>
</head>
<body>
<div class="stage">

<!-- ============ dark theme ============ -->
<main class="page dark">
  <header class="abs site-header"></header>
  <div class="abs brand"><i></i>KVR GLOBALINKS</div>
  <div class="abs login">Login</div>
  <div class="abs lang"><b></b>English ⌄</div>
  <nav class="abs nav"><span class="active">Home</span><span>About</span><span>Services</span><span>Our Products</span><span>Portfolio</span><span>Blog</span><span>Contact Us</span>
    <svg width="9" height="9" viewBox="0 0 10 10"><circle cx="4" cy="4" r="3" fill="none" stroke="#fff" stroke-width="1.5"/><path d="M6.3 6.3 9 9" stroke="#fff" stroke-width="1.5"/></svg></nav>

  <section class="abs hero" role="img" aria-label="Container ship at a port at sunset with cranes and a cargo plane overhead"></section>
  <h1 class="abs hero-title">KVR GLOBALINKS</h1>
  <p class="abs hero-text">Lorem ipsum dolor sit amet, consectetur adipiscing elit, sed do eiusmod tempor incididunt ut labore et dolore magna aliqua.</p>
  <div class="abs hero-btn btn-solid">GET STARTED ➜</div>
  <div class="abs arrow-ring" style="left:17px;top:204px"></div>
  <div class="abs arrow-ring" style="left:601px;top:204px"></div>

  <section class="abs services"></section>
  <h2 class="abs sec-title" style="top:424px">OUR SERVICES</h2>
  <p class="abs sec-text" style="left:100px;top:454px;width:439px">Lorem ipsum dolor sit amet, consectetur adipiscing elit, sed do eiusmod tempor incididunt ut labore et dolore magna aliqua. Ut enim ad minim veniam, quis nostrud exercitation ullamco laboris</p>
  <div class="abs tabs">
    <div class="tab on"><svg width="20" height="16"><rect x="1" y="4" width="18" height="10" fill="none" stroke="#fff"/><path d="M1 8h18" stroke="#fff"/></svg>International Trading<br>Services</div>
    <div class="tab"><svg width="16" height="20"><rect x="1" y="2" width="14" height="17" fill="none" stroke="currentColor"/><path d="M4 7h8M4 11h8M4 15h6" stroke="currentColor"/></svg>International Contracting<br>Services</div>
  </div>
  <div class="abs svc-card" style="left:59px"><div class="svc-icon"><svg width="49" height="49"><rect x="15" y="20" width="19" height="13" fill="none" stroke="#fff" stroke-width="1.5"/><path d="M18 20v-5h13v5" fill="none" stroke="#fff" stroke-width="1.5"/></svg></div><h3>Food Products</h3><p>Sed ut perspiciatis unde omnis iste natus error voluptatem</p></div>
  <div class="abs svc-card" style="left:193px"><div class="svc-icon"><svg width="49" height="49"><path d="M17 34V16h15v18M17 22h15M17 28h15M24 16v18" fill="none" stroke="#fff" stroke-width="1.5"/></svg></div><h3>Machinery</h3><p>Sed ut perspiciatis unde omnis iste natus error voluptatem</p></div>
  <div class="abs svc-card" style="left:326px"><div class="svc-icon"><svg width="49" height="49"><path d="M15 34l10-20 10 20M19 26h12M25 14v20" fill="none" stroke="#fff" stroke-width="1.5"/></svg></div><h3>Oil</h3><p>Sed ut perspiciatis unde omnis iste natus error voluptatem</p></div>
  <div class="abs svc-card" style="left:459px"><div class="svc-icon"><svg width="49" height="49"><path d="M24.5 13c5 6 7 10 7 14a7 7 0 0 1-14 0c0-4 2-8 7-14z" fill="none" stroke="#fff" stroke-width="1.5"/></svg></div><h3>Energy &amp; Gas</h3><p>Sed ut perspiciatis unde omnis iste natus error voluptatem</p></div>
  <div class="abs btn-line" style="left:272px;top:762px;width:94px;height:28px">LEARN MORE ⊙</div>

  <section class="abs band" role="img" aria-label="Yellow mining excavator loading rocks in a quarry"></section>
  <div class="abs play"><svg width="44" height="44"><path d="M17 13l14 9-14 9z" fill="var(--red)"/></svg></div>
  <p class="abs band-text">Take Your Business to a New Height<br>With the Help of Our Export Import Products</p>

  <section class="abs about"></section>
  <div class="abs about-photo"><div role="img" aria-label="Aerial view of a cargo ship loaded with containers"></div></div>
  <h2 class="abs about-title">ABOUT OUR COMPANY</h2>
  <p class="abs about-text">Sed ut perspiciatis unde omnis iste natus sit voluptatem accusantium doloremque laudantium, totam rem aperiam, eaque ipsa quae inventore veritatis et quasi architecto beatae vitae dicta sunt explicabo. ipsam voluptatem quia voluptas sit aspernatur aut odit aut fugit, sed quia consequuntur magni dolores qui ratione voluptatem nesciunt. Neque porro quisquam est, qui dolorem ipsum quia dolor amet, consectetur, adipisci velit, sed quia non numquam eius modi tempora.</p>
  <div class="abs about-btn btn-solid">LEARN MORE ➜</div>

  <section class="abs feature-band"></section>
  <section class="abs feature-base"></section>
  <h2 class="abs sec-title feature-title" style="top:1495px">FEATURED PROJECTS</h2>
  <p class="abs sec-text" style="left:90px;top:1526px;width:459px;color:#fff">Sed ut perspiciatis unde omnis iste natus error sit voluptatem accusantium doloremque laudantium, totam rem aperiam, eaque ipsa quae ab illo inventore veritatis et quasi archi beatae vitae dicta sunt explicabo.</p>
  <span class="abs chev" style="left:22px;top:1577px">‹</span><span class="abs chev" style="left:603px;top:1577px">›</span>
  <article class="abs proj" style="left:59px"><div role="img" aria-label="Aerial view of an industrial complex" style="height:100%;background:linear-gradient(180deg,#8a8f93,#5e6468)"></div><div class="cap"><h4>Lorem ipsum dolor sit amet</h4><p>Sed ut perspiciatis unde omnis<br>iste natus error sit accusantium totam</p></div></article>
  <article class="abs proj" style="left:240px"><div role="img" aria-label="Yellow crane among tall trees" style="height:100%;background:linear-gradient(160deg,#5b6b63,#2f3a36 60%,#8c8a2c)"></div><div class="cap"><h4>Lorem ipsum dolor sit amet</h4><p>Sed ut perspiciatis unde omnis<br>iste natus error sit accusantium totam</p></div></article>
  <article class="abs proj" style="left:420px"><div role="img" aria-label="Offshore oil rig at sea" style="height:100%;background:linear-gradient(180deg,#7d8788,#3f4a4c)"></div><div class="cap"><h4>Lorem ipsum dolor sit amet</h4><p>Sed ut perspiciatis unde omnis<br>iste natus error sit accusantium totam</p></div></article>

  <h2 class="abs sec-title" style="top:1798px">OUR NEWS</h2>
  <article class="abs news" style="left:59px"><div class="img" role="img" aria-label="Businesspeople working at a laptop" style="background:linear-gradient(135deg,#d9d3c8,#7f8d9c)"><span class="date">▦ Jan 10, 2020</span></div><h4>Nemo enim ipsam voluptatem<br>quia voluptas sit</h4><p>Lorem ipsum dolor sit amet, consectetur adipiscing elit, sed do eiusmod</p><span class="more">READ MORE ⊙</span></article>
  <article class="abs news" style="left:237px"><div class="img" role="img" aria-label="Fresh vegetables, fruit and groceries on a table" style="background:linear-gradient(135deg,#2b2622,#8a3b25 50%,#5f7a2e)"><span class="date">▦ Dec 24, 2019</span></div><h4>Nemo enim ipsam voluptatem<br>quia voluptas sit</h4><p>Lorem ipsum dolor sit amet, consectetur adipiscing elit, sed do eiusmod</p><span class="more">READ MORE ⊙</span></article>
  <article class="abs news" style="left:415px"><div class="img" role="img" aria-label="Cargo plane over shipping containers at sunset" style="background:linear-gradient(180deg,#5f7fb8,#e3a25a 60%,#7a3d2c)"><span class="date">▦ Dec 15, 2019</span></div><h4>Nemo enim ipsam voluptatem<br>quia voluptas sit</h4><p>Lorem ipsum dolor sit amet, consectetur adipiscing elit, sed do eiusmod</p><span class="more">READ MORE ⊙</span></article>

  <footer class="abs footer" role="img" aria-label="Faint city skyline at night"></footer>
  <div class="abs foot-brand"><i></i>KVR GLOBALINKS</div>
  <div class="abs foot-contact"><span><svg width="6" height="8"><path d="M3 8C1 5 0 4 0 3a3 3 0 0 1 6 0c0 1-1 2-3 5z" fill="#fff"/></svg>123, Lorem ipsum dolor sit amet, adipiscing elit</span><span><svg width="7" height="7"><path d="M1 0h2l1 2-1 1a4 4 0 0 0 1 1l1-1 2 1v2c-4 0-7-3-7-6z" fill="#fff"/></svg>(555)014-2290</span><span><svg width="8" height="6"><rect width="8" height="6" fill="#fff"/><path d="M0 0l4 3 4-3" stroke="#111" fill="none"/></svg>hello@kvrglobalinks.com</span></div>
  <div class="abs foot-links">Home &nbsp;|&nbsp; About &nbsp;|&nbsp; Services &nbsp;|&nbsp; Our Products &nbsp;|&nbsp; Blog &nbsp;|&nbsp; Contact Us</div>
  <div class="abs foot-copy">© 2020 KVR Globalinks. All Rights Reserved &nbsp;|&nbsp; Privacy Policy &nbsp;|&nbsp; Terms &amp; Condition</div>
  <div class="abs socials"><i></i><i></i><i></i><i></i></div>
</main>

<!-- ============ light theme ============ -->
<main class="page light">
  <header class="abs site-header"></header>
  <div class="abs brand"><i></i>KVR GLOBALINKS</div>
  <div class="abs login">Login</div>
  <div class="abs lang"><b></b>English ⌄</div>
  <nav class="abs nav"><span class="active">Home</span><span>About</span><span>Services</span><span>Our Products</span><span>Portfolio</span><span>Blog</span><span>Contact Us</span>
    <svg width="9" height="9" viewBox="0 0 10 10"><circle cx="4" cy="4" r="3" fill="none" stroke="#fff" stroke-width="1.5"/><path d="M6.3 6.3 9 9" stroke="#fff" stroke-width="1.5"/></svg></nav>

  <section class="abs hero" role="img" aria-label="Container ship at a port at sunset with cranes and a cargo plane overhead"></section>
  <h1 class="abs hero-title">KVR GLOBALINKS</h1>
  <p class="abs hero-text">Lorem ipsum dolor sit amet, consectetur adipiscing elit, sed do eiusmod tempor incididunt ut labore et dolore magna aliqua.</p>
  <div class="abs hero-btn btn-solid">GET STARTED ➜</div>
  <div class="abs arrow-ring" style="left:17px;top:204px"></div>
  <div class="abs arrow-ring" style="left:601px;top:204px"></div>

  <section class="abs services"></section>
  <h2 class="abs sec-title" style="top:424px">OUR SERVICES</h2>
  <p class="abs sec-text" style="left:100px;top:454px;width:439px">Lorem ipsum dolor sit amet, consectetur adipiscing elit, sed do eiusmod tempor incididunt ut labore et dolore magna aliqua. Ut enim ad minim veniam, quis nostrud exercitation ullamco laboris</p>
  <div class="abs tabs">
    <div class="tab on"><svg width="20" height="16"><rect x="1" y="4" width="18" height="10" fill="none" stroke="#fff"/><path d="M1 8h18" stroke="#fff"/></svg>International Trading<br>Services</div>
    <div class="tab"><svg width="16" height="20"><rect x="1" y="2" width="14" height="17" fill="none" stroke="currentColor"/><path d="M4 7h8M4 11h8M4 15h6" stroke="currentColor"/></svg>International Contracting<br>Services</div>
  </div>
  <div class="abs svc-card" style="left:59px"><div class="svc-icon"><svg width="49" height="49"><rect x="15" y="20" width="19" height="13" fill="none" stroke="#fff" stroke-width="1.5"/><path d="M18 20v-5h13v5" fill="none" stroke="#fff" stroke-width="1.5"/></svg></div><h3>Food Products</h3><p>Sed ut perspiciatis unde omnis iste natus error voluptatem</p></div>
  <div class="abs svc-card" style="left:193px"><div class="svc-icon"><svg width="49" height="49"><path d="M17 34V16h15v18M17 22h15M17 28h15M24 16v18" fill="none" stroke="#fff" stroke-width="1.5"/></svg></div><h3>Machinery</h3><p>Sed ut perspiciatis unde omnis iste natus error voluptatem</p></div>
  <div class="abs svc-card" style="left:326px"><div class="svc-icon"><svg width="49" height="49"><path d="M15 34l10-20 10 20M19 26h12M25 14v20" fill="none" stroke="#fff" stroke-width="1.5"/></svg></div><h3>Oil</h3><p>Sed ut perspiciatis unde omnis iste natus error voluptatem</p></div>
  <div class="abs svc-card" style="left:459px"><div class="svc-icon"><svg width="49" height="49"><path d="M24.5 13c5 6 7 10 7 14a7 7 0 0 1-14 0c0-4 2-8 7-14z" fill="none" stroke="#fff" stroke-width="1.5"/></svg></div><h3>Energy &amp; Gas</h3><p>Sed ut perspiciatis unde omnis iste natus error voluptatem</p></div>
  <div class="abs btn-line" style="left:272px;top:762px;width:94px;height:28px">LEARN MORE ⊙</div>

  <section class="abs band" role="img" aria-label="Yellow mining excavator loading rocks in a quarry"></section>
  <div class="abs play"><svg width="44" height="44"><path d="M17 13l14 9-14 9z" fill="var(--red)"/></svg></div>
  <p class="abs band-text">Take Your Business to a New Height<br>With the Help of Our Export Import Products</p>

  <section class="abs about"></section>
  <div class="abs about-photo"><div role="img" aria-label="Aerial view of a cargo ship loaded with containers"></div></div>
  <h2 class="abs about-title">ABOUT OUR COMPANY</h2>
  <p class="abs about-text">Sed ut perspiciatis unde omnis iste natus sit voluptatem accusantium doloremque laudantium, totam rem aperiam, eaque ipsa quae inventore veritatis et quasi architecto beatae vitae dicta sunt explicabo. ipsam voluptatem quia voluptas sit aspernatur aut odit aut fugit, sed quia consequuntur magni dolores qui ratione voluptatem nesciunt. Neque porro quisquam est, qui dolorem ipsum quia dolor amet, consectetur, adipisci velit, sed quia non numquam eius modi tempora.</p>
  <div class="abs about-btn btn-solid">LEARN MORE ➜</div>

  <section class="abs feature-band"></section>
  <section class="abs feature-base"></section>
  <h2 class="abs sec-title feature-title" style="top:1495px">FEATURED PROJECTS</h2>
  <p class="abs sec-text" style="left:90px;top:1526px;width:459px;color:#fff">Sed ut perspiciatis unde omnis iste natus error sit voluptatem accusantium doloremque laudantium, totam rem aperiam, eaque ipsa quae ab illo inventore veritatis et quasi archi beatae vitae dicta sunt explicabo.</p>
  <span class="abs chev" style="left:22px;top:1577px">‹</span><span class="abs chev" style="left:603px;top:1577px">›</span>
  <article class="abs proj" style="left:59px"><div role="img" aria-label="Aerial view of an industrial complex" style="height:100%;background:linear-gradient(180deg,#8a8f93,#5e6468)"></div><div class="cap"><h4>Lorem ipsum dolor sit amet</h4><p>Sed ut perspiciatis unde omnis<br>iste natus error sit accusantium totam</p></div></article>
  <article class="abs proj" style="left:240px"><div role="img" aria-label="Yellow crane among tall trees" style="height:100%;background:linear-gradient(160deg,#5b6b63,#2f3a36 60%,#8c8a2c)"></div><div class="cap"><h4>Lorem ipsum dolor sit amet</h4><p>Sed ut perspiciatis unde omnis<br>iste natus error sit accusantium totam</p></div></article>
  <article class="abs proj" style="left:420px"><div role="img" aria-label="Offshore oil rig at sea" style="height:100%;background:linear-gradient(180deg,#7d8788,#3f4a4c)"></div><div class="cap"><h4>Lorem ipsum dolor sit amet</h4><p>Sed ut perspiciatis unde omnis<br>iste natus error sit accusantium totam</p></div></article>

  <h2 class="abs sec-title" style="top:1798px">OUR NEWS</h2>
  <article class="abs news" style="left:59px"><div class="img" role="img" aria-label="Businesspeople working at a laptop" style="background:linear-gradient(135deg,#d9d3c8,#7f8d9c)"><span class="date">▦ Jan 10, 2020</span></div><h4>Nemo enim ipsam voluptatem<br>quia voluptas sit</h4><p>Lorem ipsum dolor sit amet, consectetur adipiscing elit, sed do eiusmod</p><span class="more">READ MORE ⊙</span></article>
  <article class="abs news" style="left:237px"><div class="img" role="img" aria-label="Fresh vegetables, fruit and groceries on a table" style="background:linear-gradient(135deg,#2b2622,#8a3b25 50%,#5f7a2e)"><span class="date">▦ Dec 24, 2019</span></div><h4>Nemo enim ipsam voluptatem<br>quia voluptas sit</h4><p>Lorem ipsum dolor sit amet, consectetur adipiscing elit, sed do eiusmod</p><span class="more">READ MORE ⊙</span></article>
  <article class="abs news" style="left:415px"><div class="img" role="img" aria-label="Cargo plane over shipping containers at sunset" style="background:linear-gradient(180deg,#5f7fb8,#e3a25a 60%,#7a3d2c)"><span class="date">▦ Dec 15, 2019</span></div><h4>Nemo enim ipsam voluptatem<br>quia voluptas sit</h4><p>Lorem ipsum dolor sit amet, consectetur adipiscing elit, sed do eiusmod</p><span class="more">READ MORE ⊙</span></article>

  <footer class="abs footer"></footer>
  <div class="abs foot-brand"><i></i>KVR GLOBALINKS</div>
  <div class="abs foot-contact"><span><svg width="6" height="8"><path d="M3 8C1 5 0 4 0 3a3 3 0 0 1 6 0c0 1-1 2-3 5z" fill="#fff"/></svg>123, Lorem ipsum dolor sit amet, adipiscing elit</span><span><svg width="7" height="7"><path d="M1 0h2l1 2-1 1a4 4 0 0 0 1 1l1-1 2 1v2c-4 0-7-3-7-6z" fill="#fff"/></svg>(555)014-2290</span><span><svg width="8" height="6"><rect width="8" height="6" fill="#fff"/><path d="M0 0l4 3 4-3" stroke="#111" fill="none"/></svg>hello@kvrglobalinks.com</span></div>
  <div class="abs foot-links">Home &nbsp;|&nbsp; About &nbsp;|&nbsp; Services &nbsp;|&nbsp; Our Products &nbsp;|&nbsp; Blog &nbsp;|&nbsp; Contact Us</div>
  <div class="abs foot-copy">© 2020 KVR Globalinks. All Rights Reserved &nbsp;|&nbsp; Privacy Policy &nbsp;|&nbsp; Terms &amp; Condition</div>
  <div class="abs socials"><i></i><i></i><i></i><i></i></div>
</main>

</div>
</body>
</html>
```